Frostvale Harborline LLC

we need a business card design

Industry/Entity Type

hvac

Contact Information for Business Card

my logo

Requirements
Must have
• my logo and same colors

```html
<!DOCTYPE html>
<html lang="en">
<head>
<meta charset="utf-8">
<title>Frostvale Harborline LLC — Business Card</title>
<link rel="stylesheet" href="https://fonts.googleapis.com/css2?family=Poppins:wght@400;500;700&display=swap">
<style>
  :root {
    --page-bg: #e6e8eb;
    --card-bg: #ffffff;
    --brand-blue: #1f5fae;
    --brand-navy: #1a3f7a;
    --brand-gold: #f3b23a;
    --ink: #2a2a2a;
    --rule: #2c5fb8;
  }
  * { box-sizing: border-box; margin: 0; padding: 0; }
  html, body {
    width: 1200px; height: 874px; overflow: hidden;
    background: var(--page-bg);
    font-family: "Poppins", sans-serif;
    color: var(--ink);
  }
  .sheet {
    width: 1200px; height: 874px;
    display: flex; flex-direction: column; align-items: center; justify-content: center;
    gap: 40px;
  }
  .card {
    position: relative;
    width: 640px; height: 366px;
    background: var(--card-bg);
    border-radius: 22px;
    box-shadow: 0 6px 22px rgba(0,0,0,.18);
    overflow: hidden;
  }
  .brand-mark {
    display: flex; align-items: center; gap: 14px;
    font-weight: 700; color: var(--brand-blue);
    letter-spacing: .5px; line-height: 1.1;
  }
  .brand-mark .dot {
    flex: none; border-radius: 50%; background: var(--brand-gold);
  }
  .card-front { display: flex; align-items: center; justify-content: center; }
  .card-front .brand-mark { font-size: 36px; text-align: left; }
  .card-front .brand-mark .dot { width: 54px; height: 54px; }

  .card-back .brand-mark {
    position: absolute; top: 56px; right: 40px;
    font-size: 22px; gap: 10px;
  }
  .card-back .brand-mark .dot { width: 34px; height: 34px; }
  .accent-bar {
    position: absolute; left: 0; top: 118px;
    width: 9px; height: 56px; background: var(--brand-blue);
  }
  .holder { position: absolute; left: 34px; top: 114px; }
  .holder-name {
    font-size: 31px; font-weight: 700; color: var(--brand-blue);
    letter-spacing: .5px; line-height: 1.1;
  }
  .holder-title { font-size: 17px; font-weight: 400; color: #333; }
  .divider {
    position: absolute; left: 34px; right: 40px; top: 196px;
    height: 2px; background: var(--rule);
  }
  .contact-list {
    position: absolute; left: 34px; top: 214px;
    list-style: none; font-size: 16px; line-height: 1.65;
  }
  .contact-list li { display: flex; align-items: center; gap: 10px; }
  .contact-list svg { width: 14px; height: 14px; fill: var(--brand-blue); flex: none; }
  .company-block {
    position: absolute; right: 40px; bottom: 30px;
    text-align: right; font-size: 17px; line-height: 1.45;
  }
  .company-block .company-name { font-weight: 500; color: #222; }
</style>
</head>
<body>
<main class="sheet">
  <section class="card card-front">
    <div class="brand-mark"><span class="dot"></span><span>Frostvale Harborline LLC</span></div>
  </section>

  <section class="card card-back">
    <div class="brand-mark"><span class="dot"></span><span>Frostvale Harborline LLC</span></div>
    <div class="accent-bar"></div>
    <div class="holder">
      <h1 class="holder-name">DANIEL WHITFORD</h1>
      <p class="holder-title">Managing Director</p>
    </div>
    <div class="divider"></div>
    <ul class="contact-list">
      <li><svg viewBox="0 0 24 24"><path d="M6.6 10.8a15 15 0 0 0 6.6 6.6l2.2-2.2c.3-.3.7-.4 1-.2 1.1.4 2.3.6 3.6.6.6 0 1 .4 1 1V20c0 .6-.4 1-1 1A17 17 0 0 1 3 4c0-.6.4-1 1-1h3.5c.6 0 1 .4 1 1 0 1.3.2 2.5.6 3.6.1.3 0 .7-.2 1z"/></svg>+1 555-014-2290</li>
      <li><svg viewBox="0 0 24 24"><path d="M2 5h20v14H2z M2 5l10 7 10-7" /></svg>dan@frostvaleharbor.com</li>
      <li><svg viewBox="0 0 24 24"><circle cx="12" cy="12" r="10"/></svg>www.frostvaleharborline.com</li>
    </ul>
    <div class="company-block">
      <p class="company-name">Frostvale Harborline</p>
      <p>Bayhaven, FL, USA</p>
    </div>
  </section>
</main>
</body>
</html>
```